Moravel Aesthetic Doctor

I require an elegant, luxurious looking business card for my aesthetic business. I am a doctor and that will set me aside from competitors. I am planning to provide home and spa based treatments to clients with high expectations. I have attached my logo.

```html
<!DOCTYPE html>
<html lang="en">
<head>
<meta charset="utf-8">
<title>Moravel Aesthetic Doctor – Business Card</title>
<link href="https://fonts.googleapis.com/css2?family=Roboto:ital,wght@0,300;0,400;1,400&display=swap" rel="stylesheet">
<style>
  :root {
    --page-bg: #e9e4dd;
    --card-bg: #f3f5f6;
    --brand-blue: #4fb0da;
    --brand-blue-deep: #2f8fbd;
    --swoosh-grey: #8e969d;
    --ink: #3a3d40;
    --ink-soft: #6f757b;
    --white: #ffffff;
  }
  * { box-sizing: border-box; margin: 0; padding: 0; }
  html, body {
    width: 1200px; height: 1054px; overflow: hidden;
    background: var(--page-bg);
    font-family: "Roboto", Arial, sans-serif;
  }
  .card {
    position: absolute; left: 100px; top: 227px;
    width: 1000px; height: 600px;
    background: var(--card-bg);
    border-radius: 22px; overflow: hidden;
    box-shadow: 0 10px 30px rgba(0,0,0,.12);
  }
  .card-waves { position: absolute; inset: 0; }
  .tagline {
    position: absolute; left: 54px; top: 46px;
    color: var(--white); font-weight: 300; font-size: 26px; line-height: 36px;
  }
  .brand {
    position: absolute; left: 390px; top: 210px;
    display: flex; align-items: center; gap: 24px;
  }
  .brand-mark {
    flex: none;
    width: 100px; height: 100px; border-radius: 50%;
    border: 3px solid var(--ink-soft);
  }
  .brand-name {
    color: var(--ink-soft); font-weight: 300; font-size: 38px;
    white-space: nowrap; line-height: 1;
  }
  .social {
    position: absolute; left: 54px; top: 398px;
    display: flex; align-items: center; gap: 10px;
    font-size: 23px; color: var(--ink);
  }
  .social-dot { width: 24px; height: 24px; border-radius: 50%; background: var(--brand-blue); }
  .social-dot:first-of-type { margin-left: 8px; }
  .contact { position: absolute; left: 54px; top: 455px; list-style: none; }
  .contact li {
    display: flex; align-items: center; gap: 18px;
    font-size: 24px; color: var(--ink); height: 38.5px;
  }
  .contact svg { width: 22px; height: 22px; fill: var(--brand-blue-deep); }
  .doctor {
    position: absolute; right: 52px; top: 400px; text-align: right;
  }
  .doctor-name { font-size: 36px; color: var(--ink); font-weight: 400; }
  .doctor-post { font-size: 19px; font-style: italic; color: var(--brand-blue-deep); margin-top: 6px; }
  .doctor-diploma { font-size: 23px; color: var(--brand-blue-deep); line-height: 33px; margin-top: 16px; }
</style>
</head>
<body>
<main class="card">
  <svg class="card-waves" viewBox="0 0 1000 600" preserveAspectRatio="none" aria-hidden="true">
    <path d="M0 0 H1000 V40 C830 20 700 40 560 90 C400 145 220 160 0 150 Z" fill="var(--brand-blue)"/>
    <path d="M0 158 C230 172 410 150 560 100 C700 55 830 30 1000 48 V66 C840 50 720 72 580 118 C420 170 230 186 0 176 Z" fill="var(--swoosh-grey)"/>
    <path d="M500 90 C640 40 800 20 1000 28" stroke="var(--white)" stroke-width="5" fill="none"/>
  </svg>

  <p class="tagline">Home and Spa<br>Based Treatments</p>

  <div class="brand">
    <span class="brand-mark"></span>
    <p class="brand-name">Moravel Aesthetic Doctor</p>
  </div>

  <div class="social">Follow us on: <span class="social-dot"></span><span class="social-dot"></span></div>

  <ul class="contact">
    <li><svg viewBox="0 0 24 24"><path d="M6.6 10.8a15 15 0 0 0 6.6 6.6l2.2-2.2a1 1 0 0 1 1-.25 11.4 11.4 0 0 0 3.6.57 1 1 0 0 1 1 1V20a1 1 0 0 1-1 1A17 17 0 0 1 3 4a1 1 0 0 1 1-1h3.5a1 1 0 0 1 1 1c0 1.25.2 2.45.57 3.57a1 1 0 0 1-.25 1z"/></svg>0800 555 014</li>
    <li><svg viewBox="0 0 24 24"><path d="M2 5h20v14H2z M4 7v1l8 5 8-5V7l-8 5z" fill-rule="evenodd"/></svg>elise@moravel.co.nz</li>
    <li><svg viewBox="0 0 24 24"><path d="M12 2a10 10 0 1 0 0 20 10 10 0 0 0 0-20zm0 2c.9 1 1.7 2.6 2 4.5h-4c.3-1.9 1.1-3.5 2-4.5zM4.3 10.5h3.6a16 16 0 0 0 0 3H4.3a8 8 0 0 1 0-3zm5.6 0h4.2a14 14 0 0 1 0 3H9.9a14 14 0 0 1 0-3zm6.2 0h3.6a8 8 0 0 1 0 3h-3.6a16 16 0 0 0 0-3zM10 15.5h4c-.3 1.9-1.1 3.5-2 4.5-.9-1-1.7-2.6-2-4.5z"/></svg>www.moravel.co.nz</li>
  </ul>

  <div class="doctor">
    <h1 class="doctor-name">Dr Elise Varden</h1>
    <p class="doctor-post">MRCPCH MD</p>
    <p class="doctor-diploma">Australasian Diploma of<br>Aesthetic Medicine</p>
  </div>
</main>
</body>
</html>
```